Business Card Design

Extremely classy understated design.

Printing in fancy scrip or hand writing.

Conservative color scheme such as black print on beige paper. I am sure you have much better ideas than I would have.

I am involved in a number of different businesses and require a simple elegant business card.

I would like a object on the card, such as, a bald eagle, an antique Halden Crestor, a water fall or a beautiful flower.

My name is: Dwight L. Kessler Not Dwight L. Kessler Investments Investments is my occupation Most of the designs are not acceptable. Very disappointed with results.

Industry/Entity Type

Business

Contact Information for Business Card

Dwight L Kessler
Investments
702 555 0187
mirewoodlk@postvane.net

```html
<!DOCTYPE html>
<html lang="en">
<head>
<meta charset="utf-8">
<title>Dwight L Kessler — Business Card</title>
<link rel="stylesheet" href="https://fonts.googleapis.com/css2?family=Great+Vibes&family=Open+Sans:wght@400;600&display=swap">
<style>
  :root {
    --page: #ffffff;
    --silver-light: #f2f2f2;
    --silver-mid: #c9c9c9;
    --silver-dark: #a6a6a6;
    --ink: #1a1a1a;
    --card-black: #0b0b0b;
    --pattern-dark: #151515;
    --pattern-mid: #262626;
    --gold-light: #f0d27a;
    --gold: #c9a03c;
    --gold-deep: #8a6a1e;
    --name-silver: #d6d6d6;
    --contact: #e8e8e8;
  }
  * { box-sizing: border-box; margin: 0; padding: 0; }
  html, body {
    width: 1200px; height: 900px; overflow: hidden;
    background: var(--page);
  }
  .stage {
    position: relative; width: 1200px; height: 900px;
  }
  .card {
    position: absolute; top: 290px;
    width: 540px; height: 320px;
    border-radius: 24px; overflow: hidden;
    box-shadow: 0 6px 18px rgba(0,0,0,0.18);
  }
  /* Back side */
  .card--back {
    left: 40px;
    background: linear-gradient(180deg, var(--silver-mid) 0%, var(--silver-light) 48%, var(--silver-dark) 100%);
    display: flex; align-items: center; justify-content: center;
  }
  .back-lines {
    font-family: "Open Sans", sans-serif;
    font-size: 19px; line-height: 1.25;
    color: var(--ink); text-align: center;
  }
  /* Front side */
  .card--front {
    left: 620px;
    background: var(--card-black);
  }
  .damask-field {
    position: absolute; inset: 0;
    background: radial-gradient(ellipse at 55% 45%, var(--pattern-mid) 0%, var(--pattern-dark) 55%, var(--card-black) 100%);
  }
  .ornament {
    position: absolute; left: 50%; width: 180px; height: 70px;
    margin-left: -60px;
    border-radius: 50% 50% 40% 40%;
    background: radial-gradient(ellipse at 50% 50%, var(--gold-light) 0%, var(--gold) 45%, var(--gold-deep) 80%, transparent 100%);
    opacity: 0.9;
  }
  .ornament--top { top: 38px; }
  .ornament--bottom { top: 205px; border-radius: 40% 40% 50% 50%; }
  .name-band {
    position: absolute; left: 0; right: 0; top: 112px; height: 78px;
    background: var(--card-black);
    border-top: 2px solid var(--gold);
    border-bottom: 2px solid var(--gold);
  }
  .name-block {
    position: absolute; left: 0; right: 0; top: 116px;
    padding-left: 60px;
    text-align: center;
  }
  .name {
    font-family: "Great Vibes", cursive;
    font-size: 50px; line-height: 1;
    color: var(--name-silver);
  }
  .occupation {
    font-family: "Open Sans", sans-serif;
    font-size: 13px; letter-spacing: 5px;
    color: var(--name-silver);
    margin-top: -4px;
  }
  .contact {
    position: absolute; left: 34px; top: 246px;
    font-family: "Open Sans", sans-serif;
    font-size: 19px; color: var(--contact);
    line-height: 1.2;
  }
  .contact-row { display: flex; align-items: center; gap: 9px; }
  .contact-icon { width: 22px; height: 20px; flex: none; }
</style>
</head>
<body>
<main class="stage">
  <section class="card card--back" aria-label="Card back">
    <div class="back-lines">
      <p>Company Name</p>
      <p>Company Name or logo</p>
      <p>Company name</p>
      <p>Company name or logo</p>
    </div>
  </section>

  <section class="card card--front" aria-label="Card front">
    <div class="damask-field" role="img" aria-label="Dark black damask floral pattern background"></div>
    <div class="ornament ornament--top" role="img" aria-label="Gold baroque scroll ornament"></div>
    <div class="name-band"></div>
    <div class="ornament ornament--bottom" role="img" aria-label="Gold baroque scroll ornament"></div>
    <div class="name-block">
      <p class="name">Dwight L Kessler</p>
      <p class="occupation">Investments</p>
    </div>
    <div class="contact">
      <p class="contact-row">
        <svg class="contact-icon" viewBox="0 0 24 24" aria-hidden="true">
          <path fill="#c9a03c" d="M6.6 10.8c1.4 2.8 3.8 5.1 6.6 6.6l2.2-2.2c.3-.3.7-.4 1-.2 1.1.4 2.3.6 3.6.6.6 0 1 .4 1 1V20c0 .6-.4 1-1 1C10.6 21 3 13.4 3 4c0-.6.4-1 1-1h3.5c.6 0 1 .4 1 1 0 1.3.2 2.5.6 3.6.1.3 0 .7-.2 1L6.6 10.8z"/>
        </svg>
        <span>702 555 0187</span>
      </p>
      <p class="contact-row">
        <svg class="contact-icon" viewBox="0 0 24 20" aria-hidden="true">
          <rect x="1" y="3" width="22" height="15" rx="1.5" fill="#c9a03c"/>
          <path d="M1.5 4 L12 12 L22.5 4" fill="none" stroke="#0b0b0b" stroke-width="1.6"/>
        </svg>
        <span>mirewoodlk@postvane.net</span>
      </p>
    </div>
  </section>
</main>
</body>
</html>
```